Buch-/eBook-Cover für Traumatherapeutin
Zielgruppe
Ich bin Traumatherapeutin und schreibe ein Buch zum Thema Trauma bearbeiten.
Meine Zielgruppe sucht Heilung, Genesung, Selbstliebe etc.
Aufgabenstellung
Buchcover
Bitte erstell mir ein modernes positives inspirierendes Buchcover mit dem
Titel: 'Morgenlicht NEU entdecken“
Untertitel: „Spüre den Mut der ganz in dir wohnt“
Dr. Mira Kessow
Ich hätte gerne ein modernes Buch, das entweder einen Bezug zum Thema Trauma hat oder aber einfach stylische Schriftzüge. Bin aber auch offen für andere Vorschläge.
Dunkelblau, weiß und türkis oder auch rosa mag ich ganz gerne. Wobei Dunkelblau, weiß und türkis meine Favoriten sind und mit rosa höchstens kleinere Akzente gesetzt werden sollten.
Das Buchcover soll modern sein und direkt ansprechen. Gerne eine originelle Lösung, oder etwas Besonderes, etwas das Tiefe ausdrückt, oder man mehrmals hinsehen muss um etwas zu erkennen oder etwas das mehr Interpretationsspielraum lässt.
Gerne auch viel weiß, zumindest heller und nicht zu dunkel. Stylish, aber nicht überfrachtet.
Schreib mich gerne an, wenn du Fragen hast.
Ich habe mal zwei Beispiel von Typolösungen angehängt, die ich ganz cool fände.
Ich freue mich auf deine Ideen :-)
Ganz liebe Grüße
Mira

```html
<!DOCTYPE html>
<html lang="de">
<head>
<meta charset="utf-8">
<title>Morgenlicht NEU entdecken – Buchcover</title>
<link rel="stylesheet" href="https://fonts.googleapis.com/css2?family=Allura&family=Bebas+Neue&family=Open+Sans:ital,wght@0,400;1,400&display=swap">
<style>
  :root {
    --rose: #d5a2be;
    --mist: #bcc1cc;
    --teal: #add7d3;
    --teal-deep: #a7d8d2;
    --violet: #5a3a92;
    --white: #ffffff;
  }
  html, body {
    margin: 0;
    padding: 0;
    width: 858px;
    height: 1200px;
    overflow: hidden;
  }
  .cover {
    position: relative;
    width: 858px;
    height: 1200px;
    background: linear-gradient(155deg, var(--rose) 0%, var(--mist) 32%, var(--teal) 58%, var(--teal-deep) 100%);
    overflow: hidden;
  }
  .author {
    position: absolute;
    top: 46px;
    left: 0;
    width: 100%;
    text-align: center;
    font-family: "Open Sans", Arial, sans-serif;
    font-size: 24px;
    color: var(--white);
    margin: 0;
  }
  .title { margin: 0; font-weight: normal; }
  .title-script {
    position: absolute;
    font-family: "Allura", cursive;
    color: var(--violet);
    line-height: 1;
    white-space: nowrap;
  }
  .title-top {
    left: 100px;
    top: 378px;
    font-size: 110px;
  }
  .title-main {
    position: absolute;
    left: 0;
    width: 100%;
    top: 470px;
    text-align: center;
    font-family: "Bebas Neue", Impact, sans-serif;
    font-size: 250px;
    line-height: 1;
    color: var(--white);
    letter-spacing: 2px;
  }
  .title-bottom {
    right: 90px;
    top: 640px;
    font-size: 110px;
  }
  .subtitle {
    position: absolute;
    right: 112px;
    top: 764px;
    margin: 0;
    text-align: right;
    font-family: "Open Sans", Arial, sans-serif;
    font-style: italic;
    font-size: 27px;
    line-height: 1.35;
    color: var(--violet);
  }
</style>
</head>
<body>
  <main class="cover">
    <p class="author">Dr. Mira Kessow</p>
    <h1 class="title">
      <span class="title-script title-top">Morgenlicht</span>
      <span class="title-main">NEU</span>
      <span class="title-script title-bottom">entdecken</span>
    </h1>
    <p class="subtitle">Spüre den Mut der ganz<br>in dir wohnt</p>
  </main>
</body>
</html>
```